Business Card for Coastal Tundrabridge Advisory

We need a business card for Coastal Tundrabridge Advisory. The company website address is provided below. The company logo is attached. We provide specialized permafrost services to the mining, transportation, and oil & gas industries. The card should be prepared for:
Matthias Korhonen, PhD.
Coastal Tundrabridge Advisory
PO Box 418259
Quillwater, Alaska 99642
Direct: +1-907-555-0143
Email: mkorhonen@tundrabridgeadvisory.example
Website: www.coastaltundrabridgeadvisory.example

```html
<!DOCTYPE html>
<html lang="en">
<head>
<meta charset="utf-8">
<title>Coastal Tundrabridge Advisory – Business Card</title>
<link rel="stylesheet" href="https://fonts.googleapis.com/css2?family=Roboto:wght@300;400;700&display=swap">
<style>
  :root {
    --stage: #232323;
    --card: #111723;
    --ink: #ffffff;
    --ice: #3fa9e0;
    --ice-deep: #1c5a85;
    --muted: #c9d1dc;
  }
  * { box-sizing: border-box; margin: 0; padding: 0; }
  html, body { width: 1200px; height: 711px; overflow: hidden; }
  body {
    background: var(--stage);
    font-family: "Roboto", Arial, sans-serif;
    color: var(--ink);
    position: relative;
  }
  .card {
    position: absolute;
    top: 200px;
    width: 540px;
    height: 309px;
    background: var(--card);
    overflow: hidden;
  }
  .card--front { left: 40px; }
  .card--back { left: 620px; }

  .pattern-field {
    position: absolute;
    inset: 0;
    background:
      linear-gradient(200deg, rgba(63,169,224,0.75) 0%, rgba(28,90,133,0.45) 30%, rgba(17,23,35,0) 62%),
      linear-gradient(180deg, rgba(255,255,255,0.03), rgba(255,255,255,0.01));
  }
  .wordmark {
    display: flex;
    align-items: center;
    gap: 8px;
    font-weight: 700;
    text-transform: uppercase;
    color: var(--ink);
    letter-spacing: 0.04em;
  }
  .wordmark__mark {
    width: 12px; height: 12px;
    background: var(--ink);
  }
  .card--front .wordmark {
    position: absolute;
    left: 0; right: 0;
    top: 118px;
    justify-content: center;
    font-size: 24px;
  }
  .services {
    position: absolute;
    left: 0; right: 0;
    bottom: 26px;
    text-align: center;
  }
  .services__title {
    font-size: 11px;
    font-weight: 700;
    letter-spacing: 0.02em;
    margin-bottom: 4px;
  }
  .services__text { font-size: 11px; font-weight: 400; color: var(--muted); }

  .card--back .wordmark {
    position: absolute;
    right: 24px;
    top: 30px;
    font-size: 15px;
  }
  .holder {
    position: absolute;
    left: 0;
    top: 70px;
    padding-left: 24px;
    border-left: 12px solid var(--ink);
  }
  .holder__name { font-size: 27px; line-height: 1.05; }
  .holder__first { font-weight: 700; }
  .holder__last { font-weight: 300; }
  .holder__title { font-size: 18px; font-weight: 400; }

  .address {
    position: absolute;
    left: 36px;
    bottom: 26px;
    font-size: 13px;
    line-height: 1.35;
  }
  .contacts {
    position: absolute;
    right: 22px;
    bottom: 28px;
    list-style: none;
    font-size: 12px;
    line-height: 1.5;
    text-align: right;
  }
  .contacts li { display: flex; align-items: center; justify-content: flex-end; gap: 6px; }
  .contacts svg { width: 11px; height: 11px; fill: none; stroke: var(--ink); stroke-width: 1.6; }
</style>
</head>
<body>
  <section class="card card--front">
    <div class="pattern-field" role="img" aria-label="Repeating company wordmark pattern fading from ice blue to navy"></div>
    <div class="wordmark"><span class="wordmark__mark"></span>Coastal Tundrabridge Advisory</div>
    <div class="services">
      <p class="services__title">OUR SERVICES</p>
      <p class="services__text">We provide specialized permafrost services to the mining, transportation, and oil &amp; gas industries</p>
    </div>
  </section>

  <section class="card card--back">
    <div class="wordmark"><span class="wordmark__mark"></span>Coastal Tundrabridge Advisory</div>
    <div class="holder">
      <p class="holder__name"><span class="holder__first">Matthias</span> <span class="holder__last">Korhonen</span></p>
      <p class="holder__title">PhD</p>
    </div>
    <address class="address" style="font-style:normal">
      PO Box 418259<br>
      Quillwater, Alaska 99642
    </address>
    <ul class="contacts">
      <li>+1-907-555-0143
        <svg viewBox="0 0 12 12"><path d="M3 1.5l1.6 2.3-1 1.1a6 6 0 0 0 2.9 2.9l1.1-1L10 8.4 9.3 10C5 10 2 7 2 2.7z"/></svg>
      </li>
      <li>mkorhonen@tundrabridgeadvisory.example
        <svg viewBox="0 0 12 12"><rect x="1" y="2.5" width="10" height="7"/><path d="M1 2.5l5 4 5-4"/></svg>
      </li>
      <li>www.coastaltundrabridgeadvisory.example
        <svg viewBox="0 0 12 12"><circle cx="6" cy="6" r="5"/><ellipse cx="6" cy="6" rx="2" ry="5"/><path d="M1 6h10"/></svg>
      </li>
    </ul>
  </section>
</body>
</html>
```